Web Developer Needs a Business Card Design

I need a personal business card design that represents me as a web developer for potential employers. I would like the background to be a dark color on the front for contrast with my logo and name. The back will have all my information along with a smaller version of the logo. I want something with a modern look and feel, not too conservative. This will be used for potential employers and freelance work.

Industry/Entity Type

Business

Contact Information for Business Card

Front should have my logo and name. The back should have all my personal information which would include: name: Tom Varulek, phone: 570-614-3098, email: tomvarulek@quillbox.net, website url: www.tomvarulek.net, logo, web developer.

Font styles to use
Sans Serif

Requirements
Must have
• Must include my logo. The color palette base color will be the logo color.

```html
<!DOCTYPE html>
<html lang="en">
<head>
<meta charset="utf-8">
<title>Tom Varulek — Business Card</title>
<link rel="stylesheet" href="https://fonts.googleapis.com/css2?family=Open+Sans:wght@300;400;600;700&display=swap">
<style>
  :root {
    --teal: #7fd3c0;
    --teal-deep: #5fbfa9;
    --ink: #2b2b2b;
    --coal: #1f1f1f;
    --coal-light: #3a3a3a;
    --paper: #ffffff;
    --backdrop: #ecebe8;
    --muted: #444444;
  }
  * { box-sizing: border-box; margin: 0; padding: 0; }
  html, body {
    width: 1200px;
    height: 913px;
    overflow: hidden;
  }
  body {
    background: var(--backdrop);
    font-family: "Open Sans", sans-serif;
    position: relative;
  }
  .card {
    position: absolute;
    top: 308px;
    width: 520px;
    height: 297px;
    border-radius: 18px;
    overflow: hidden;
    box-shadow: 0 10px 28px rgba(0,0,0,0.18);
  }

  /* Back side: contact details */
  .card--back {
    left: 50px;
    background: var(--paper);
  }
  .card--back .wave {
    position: absolute;
    inset: 0;
    width: 100%;
    height: 100%;
  }
  .identity {
    position: absolute;
    left: 34px;
    top: 108px;
  }
  .identity__name {
    font-weight: 700;
    font-size: 21px;
    letter-spacing: 0.5px;
    color: var(--ink);
    text-transform: uppercase;
  }
  .identity__role {
    font-weight: 600;
    font-size: 14px;
    letter-spacing: 0.8px;
    color: var(--teal-deep);
    text-transform: uppercase;
    margin-top: -2px;
  }
  .divider {
    position: absolute;
    left: 0;
    top: 172px;
    width: 300px;
    height: 1.5px;
    background: var(--ink);
  }
  .contact {
    position: absolute;
    left: 34px;
    top: 190px;
    list-style: none;
  }
  .contact__item {
    display: flex;
    align-items: center;
    gap: 8px;
    font-size: 13.5px;
    line-height: 20px;
    color: var(--muted);
  }
  .contact__icon {
    width: 11px;
    height: 11px;
    flex: none;
  }
  .brandmark {
    position: absolute;
    display: flex;
    align-items: center;
    justify-content: center;
    border-radius: 50%;
    border: 9px solid var(--teal);
    color: var(--teal);
    font-weight: 600;
    text-align: center;
    line-height: 1.15;
  }
  .card--back .brandmark {
    right: 38px;
    top: 24px;
    width: 158px;
    height: 158px;
    font-size: 19px;
  }

  /* Front side: logo and name */
  .card--front {
    left: 630px;
    background: linear-gradient(160deg, var(--coal-light) 0%, var(--coal) 70%);
    text-align: center;
  }
  .card--front .brandmark {
    left: 50%;
    top: 38px;
    transform: translateX(-50%);
    width: 104px;
    height: 104px;
    border-width: 6px;
    font-size: 13px;
  }
  .front__name {
    position: absolute;
    left: 0;
    right: 0;
    top: 168px;
    font-weight: 300;
    font-size: 32px;
    letter-spacing: 2px;
    color: var(--paper);
    text-transform: uppercase;
  }
  .front__role {
    position: absolute;
    left: 0;
    right: 0;
    top: 218px;
    font-weight: 400;
    font-size: 15px;
    letter-spacing: 0.5px;
    color: #d9d9d9;
  }
</style>
</head>
<body>

  <section class="card card--back" aria-label="Card back with contact details">
    <svg class="wave" viewBox="0 0 520 297" preserveAspectRatio="none" aria-hidden="true">
      <path d="M0,282 C150,282 330,226 520,144 L520,156 C330,236 150,290 0,290 Z" fill="var(--teal)"/>
      <path d="M0,290 C150,290 330,236 520,156 L520,297 L0,297 Z" fill="var(--coal)"/>
    </svg>

    <div class="identity">
      <p class="identity__name">Tom Varulek</p>
      <p class="identity__role">Web Developer</p>
    </div>

    <div class="divider"></div>

    <ul class="contact">
      <li class="contact__item">
        <svg class="contact__icon" viewBox="0 0 12 12" aria-hidden="true"><path d="M2.5 1 L4.5 1 L5.2 3.4 L4 4.4 C4.6 5.8 6.2 7.4 7.6 8 L8.6 6.8 L11 7.5 L11 9.5 C11 10.3 10.3 11 9.5 11 C5 11 1 7 1 2.5 C1 1.7 1.7 1 2.5 1 Z" fill="var(--teal-deep)"/></svg>
        570-614-3098
      </li>
      <li class="contact__item">
        <svg class="contact__icon" viewBox="0 0 12 12" aria-hidden="true"><rect x="0.8" y="2.3" width="10.4" height="7.4" fill="none" stroke="var(--teal-deep)" stroke-width="1.3"/><path d="M1 2.6 L6 6.6 L11 2.6" fill="none" stroke="var(--teal-deep)" stroke-width="1.3"/></svg>
        tomvarulek@quillbox.net
      </li>
      <li class="contact__item">
        <svg class="contact__icon" viewBox="0 0 12 12" aria-hidden="true"><circle cx="6" cy="6" r="5" fill="none" stroke="var(--teal-deep)" stroke-width="1.2"/><ellipse cx="6" cy="6" rx="2.2" ry="5" fill="none" stroke="var(--teal-deep)" stroke-width="1"/><path d="M1 6 H11" stroke="var(--teal-deep)" stroke-width="1"/></svg>
        www.tomvarulek.net
      </li>
    </ul>

    <div class="brandmark">Tom<br>Varulek</div>
  </section>

  <section class="card card--front" aria-label="Card front with name">
    <div class="brandmark">Tom<br>Varulek</div>
    <p class="front__name">Tom Varulek</p>
    <p class="front__role">Front-End Developer</p>
  </section>

</body>
</html>
```